Flat bootstrap design for existing site

I'm looking for a modern flat design based around an existing logo. This has to be a custom design (no external templates), and implemented into a bootstrap framework.

The logo is attached as 2 versions - choose whichever you want, that flows better with whatever design you choose.

Added screenshots of the existing site (currently using the default bootstrap layouts). Please make your designs around those pages in the screenshots (i.e. the homepage only has the postal code input and the header). The active page has 3 screenshots, because I wanted to illustrate the other states that would be visible (in the table rows).

This is a moving/junk removal website, just for some context.

Here's some example websites (flat designs) that I like, just to give you an idea of what I'm after.

https://www.plimvora.com/
https://dacklow.com/
https://trevanu.com/
https://quobrintal.com/en/

Coding

Coded - Design and coding required

Number of Pages Required

5+ page

Colors

Designer to choose colors to be used in the design.

Requirements
Must have
• It must be a modern/simple flat design, that is built around the existing logo (attached).
• It has to be implemented using bootstrap.

```html
<!DOCTYPE html>
<html lang="en">
<head>
<meta charset="utf-8">
<title>Kelvora – Junk removal</title>
<link rel="stylesheet" href="https://fonts.googleapis.com/css2?family=Montserrat:wght@400;600;700&family=Open+Sans:wght@300&display=swap">
<style>
  :root {
    --brand-blue: #4ac6f3;
    --accent-orange: #f7931e;
    --text-dark: #333333;
    --text-muted: #777777;
    --placeholder: #a9a9a9;
    --white: #ffffff;
    --scene-green: #d9ebc6;
    --scene-grey: #e6e6e6;
    --ground: #cfcfcf;
  }
  * { box-sizing: border-box; margin: 0; padding: 0; }
  html, body { width: 1200px; height: 621px; overflow: hidden; background: var(--white); }
  body { position: relative; font-family: "Montserrat", sans-serif; color: var(--text-dark); }

  .site-header {
    position: absolute; left: 0; top: 0; width: 1200px; height: 94px;
    background: var(--white); box-shadow: 0 2px 8px rgba(0,0,0,0.08); z-index: 2;
  }
  .brand {
    position: absolute; left: 144px; top: 26px;
    display: flex; align-items: center; gap: 10px;
    font-family: "Montserrat", sans-serif; font-weight: 700; font-size: 34px;
    color: var(--brand-blue); letter-spacing: 0.5px;
  }
  .brand-dot { width: 16px; height: 16px; border-radius: 50%; background: var(--brand-blue); }

  .main-nav { position: absolute; top: 0; left: 0; }
  .nav-link {
    position: absolute; top: 38px; font-size: 14px; color: var(--text-muted);
    text-decoration: none; white-space: nowrap;
  }
  .nav-link.is-active::after {
    content: ""; position: absolute; left: 50%; top: 23px; width: 13px; height: 2px;
    margin-left: -6px; background: var(--accent-orange);
  }
  .btn-signin {
    position: absolute; left: 975px; top: 30px; width: 81px; height: 34px;
    background: var(--brand-blue); color: var(--white); border-radius: 2px;
    font-size: 14px; font-weight: 600; text-align: center; line-height: 34px; text-decoration: none;
  }

  .hero-title {
    position: absolute; left: 0; top: 166px; width: 1200px; text-align: center;
    font-family: "Open Sans", sans-serif; font-weight: 300; font-size: 51px; line-height: 51px;
    color: var(--text-dark); letter-spacing: -1px;
  }

  .booking-form {
    position: absolute; left: 456px; top: 290px; width: 289px; height: 58px;
    background: var(--white); border-radius: 3px;
    box-shadow: 0 6px 18px rgba(0,0,0,0.12);
  }
  .postal-input {
    position: absolute; left: 15px; top: 20px; font-size: 13px; color: var(--placeholder);
  }
  .btn-book {
    position: absolute; left: 188px; top: 4px; width: 97px; height: 50px;
    background: var(--accent-orange); color: var(--white); border-radius: 2px;
    font-size: 16px; font-weight: 700; text-align: center; line-height: 50px;
  }

  .street-scene {
    position: absolute; left: 66px; top: 370px; width: 1054px; height: 160px;
    background: linear-gradient(90deg, var(--scene-green) 0%, var(--scene-grey) 14%, #f2efe6 40%, var(--scene-grey) 70%, var(--scene-green) 100%);
    opacity: 0.7; border-radius: 4px;
  }
  .ground-line { position: absolute; left: 66px; top: 530px; width: 1054px; height: 2px; background: var(--ground); }

  .site-footer {
    position: absolute; left: 0; top: 556px; width: 1200px; height: 65px; background: var(--brand-blue);
  }
  .copyright { position: absolute; left: 144px; top: 24px; font-size: 13px; color: var(--white); }
  .social-links { position: absolute; left: 957px; top: 23px; display: flex; gap: 21px; }
  .social-link { width: 19px; height: 19px; border-radius: 50%; background: var(--white); display: block; }
</style>
</head>
<body>
  <header class="site-header">
    <div class="brand"><span class="brand-dot"></span>Kelvora</div>
    <nav class="main-nav">
      <a class="nav-link" style="left:665px" href="#">Book</a>
      <a class="nav-link" style="left:731px" href="#">How it works</a>
      <a class="nav-link is-active" style="left:848px" href="#">Become a driver</a>
    </nav>
    <a class="btn-signin" href="#">Signin</a>
  </header>

  <h1 class="hero-title">Need junk removed?<br>Book now.</h1>

  <div class="booking-form">
    <span class="postal-input">Postal Code</span>
    <span class="btn-book">Book</span>
  </div>

  <div class="street-scene" role="img" aria-label="Line illustration of a street with trees, recycling bins, a worker and a garbage truck"></div>
  <div class="ground-line"></div>

  <footer class="site-footer">
    <p class="copyright">© 2017 Kelvora. All rights reserved.</p>
    <div class="social-links">
      <a class="social-link" href="#" aria-label="Social profile 1"></a>
      <a class="social-link" href="#" aria-label="Social profile 2"></a>
      <a class="social-link" href="#" aria-label="Social profile 3"></a>
    </div>
  </footer>
</body>
</html>
```